Sickle Cell Patient Flyer

I need this be appealing to families dealing with sickle cell disease. Both informative-introducing the idea that a stroke prevention program is not only easy for their children but necessary. Stroke is a risk to all with children with SCD.
I included a few info flyers from the Vessel Alliance and licensed to me photos I like. I am open to suggestions.
web address is brightpathwellbeing.net
Call to schedule 833-412-7086
TCD is a safe and accurate tool that makes stroke prevention possible for your SCD patients and family.
Risk is highest for SCD sufferers age 2 to 5. Protect your childs future.

Target Market(s)

Parents, families and medical professionals

Industry/Entity Type

Medical wellness

Font styles to use
Other font styles liked:
• something close to my logo font

Colors
0094D4
00A9DD
6FCCEA
C7EBF8
E9F6FB

Requirements
Nice to have
• pictures of kids (Children of color) pictures of Brains, kids happy with medical professionals
Should not have
• dark colors

```html
<!DOCTYPE html>
<html lang="en">
<head>
<meta charset="UTF-8">
<title>Stroke Prevention for Children with Sickle Cell Disease</title>
<link href="https://fonts.googleapis.com/css2?family=Mystery+Quest&family=Poppins:wght@400;500;600;700&display=swap" rel="stylesheet">
<style>
  :root {
    --page-bg: #0d0c35;
    --sky-light: #E9F6FB;
    --sky-pale: #C7EBF8;
    --sky-mid: #6FCCEA;
    --sky-deep: #00A9DD;
    --navy: #1d4c85;
    --navy-dark: #164477;
    --footer-light: #5aa9dc;
    --white: #ffffff;
    --ink-soft: #2d4f77;
  }
  * { margin: 0; padding: 0; box-sizing: border-box; }
  html, body { width: 1200px; height: 1200px; overflow: hidden; }
  body { background: var(--page-bg); font-family: "Poppins", sans-serif; position: relative; }

  .flyer {
    position: absolute; left: 168px; top: 45px; width: 864px; height: 1110px;
    background: var(--sky-light); overflow: hidden;
  }

  /* Hero */
  .hero { position: absolute; left: 0; top: 0; width: 864px; height: 467px; background: var(--sky-light); }
  .brand {
    position: absolute; left: 26px; top: 40px; display: flex; align-items: center; gap: 10px;
    font-family: "Mystery Quest", cursive; font-size: 34px; line-height: 1.05; color: var(--navy);
  }
  .brand-mark { width: 18px; height: 18px; background: var(--sky-deep); flex: none; }
  .hero-title {
    position: absolute; left: 26px; top: 225px; width: 440px;
    font-family: "Mystery Quest", cursive; font-size: 33px; line-height: 38px; color: var(--navy);
    font-weight: 400;
  }
  .hero-sub {
    position: absolute; left: 26px; top: 390px; width: 340px;
    font-size: 17px; line-height: 23px; color: var(--ink-soft); font-weight: 400;
  }
  .hero-photo { position: absolute; left: 314px; top: 3px; width: 550px; height: 470px; }

  /* Info section */
  .info { position: absolute; left: 0; top: 478px; width: 864px; height: 486px; background: var(--sky-mid); }
  .info-rule { position: absolute; left: 0; top: 467px; width: 864px; height: 11px; background: var(--white); }

  .pill {
    position: absolute; left: 50%; transform: translateX(-50%);
    background: var(--navy); color: var(--white); border-radius: 8px;
    font-family: "Mystery Quest", cursive; font-size: 26px; line-height: 32px;
    padding: 0 22px; height: 32px; text-align: center; white-space: nowrap;
  }
  .pill-features { top: 12px; width: 169px; }
  .pill-facts { top: 147px; width: 170px; }

  .feature-card {
    position: absolute; top: 56px; width: 345px; height: 70px;
    background: rgba(255,255,255,0.22); border-radius: 8px;
    display: flex; align-items: center; padding-left: 15px;
  }
  .feature-left { left: 66px; }
  .feature-right { left: 450px; }
  .feature-icon { width: 54px; height: 54px; flex: none; }
  .feature-divider { width: 3px; height: 44px; background: var(--navy); margin: 0 12px 0 12px; flex: none; }
  .feature-text { color: var(--white); font-size: 15px; line-height: 19px; font-weight: 500; }

  .fact { position: absolute; display: flex; align-items: flex-start; }
  .fact-icon { width: 46px; height: 46px; flex: none; margin-top: 0; }
  .fact-text {
    color: var(--white); font-size: 15.5px; line-height: 18px; font-weight: 500;
    text-align: justify; text-align-last: left;
  }
  .fact-left { left: 40px; }
  .fact-left .fact-text { width: 308px; margin-left: 18px; }
  .fact-right { left: 452px; }
  .fact-right .fact-text { width: 308px; margin-left: 18px; }

  /* Lower band */
  .closing { position: absolute; left: 0; top: 964px; width: 864px; height: 99px; background: var(--sky-pale); }
  .callout {
    position: absolute; left: 87px; top: 932px; width: 689px; height: 68px;
    border: 1.5px solid var(--white); border-radius: 10px; padding: 5px;
  }
  .callout-inner {
    width: 100%; height: 100%; background: var(--white); border-radius: 7px;
    text-align: center; color: var(--navy); padding-top: 5px;
  }
  .callout-head { font-size: 15.5px; line-height: 22px; font-weight: 600; }
  .callout-body { font-size: 16px; line-height: 24px; font-weight: 400; }
  .tagline {
    position: absolute; left: 0; top: 1010px; width: 864px; text-align: center;
    font-family: "Mystery Quest", cursive; font-size: 34px; line-height: 40px; color: var(--navy);
    display: flex; justify-content: center; align-items: center; gap: 26px;
  }
  .tagline-star { width: 18px; height: 18px; fill: var(--white); }

  /* Footer */
  .footer { position: absolute; left: 0; top: 1063px; width: 864px; height: 47px; }
  .footer-band { position: absolute; inset: 0; }
  .footer-web {
    position: absolute; left: 59px; top: 0; height: 47px; line-height: 47px;
    color: var(--white); font-size: 15px;
  }
  .footer-web strong, .footer-call strong { font-weight: 700; }
  .footer-call {
    position: absolute; left: 461px; top: 0; height: 44px; line-height: 44px;
    color: var(--white); font-size: 16px;
  }
  .footer-call strong { font-size: 23px; letter-spacing: 0.5px; }
</style>
</head>
<body>
<main class="flyer">

  <section class="hero">
    <div class="brand"><span class="brand-mark"></span><span>Bright Path<br>Wellbeing</span></div>

    <svg class="hero-photo" viewBox="0 0 550 470" role="img" aria-label="Photo of a smiling girl giving a thumbs up while a doctor listens to her heart with a stethoscope">
      <defs>
        <linearGradient id="photoTone" x1="0" y1="0" x2="1" y2="1">
          <stop offset="0" stop-color="#dcdfe2"/>
          <stop offset="0.5" stop-color="#c8cdd2"/>
          <stop offset="1" stop-color="#e3e8ef"/>
        </linearGradient>
      </defs>
      <path d="M 14 230 A 70 70 0 0 1 60 115 A 95 95 0 0 1 205 45 A 85 85 0 0 1 340 25 A 85 85 0 0 1 470 95 A 70 70 0 0 1 530 215 A 70 70 0 0 1 500 330 L 492 467 L 310 467 A 55 55 0 0 1 290 375 A 75 75 0 0 1 150 340 A 70 70 0 0 1 50 330 A 60 60 0 0 1 14 230 Z"
            fill="url(#photoTone)" stroke="#ffffff" stroke-width="6"/>
    </svg>

    <h1 class="hero-title">Stroke Prevention<br>for children with<br>children with<br>Sickle Cell Disease is Possible!</h1>
    <p class="hero-sub">TCD is a safe and accurate tool that makes stroke prevention possible for your SCD patients and family</p>
  </section>

  <div class="info-rule"></div>

  <section class="info">
    <h2 class="pill pill-features">Key Features</h2>

    <div class="feature-card feature-left">
      <svg class="feature-icon" viewBox="0 0 54 54">
        <circle cx="27" cy="27" r="25" fill="#fff" stroke="#1d4c85" stroke-width="4"/>
        <circle cx="27" cy="27" r="15" fill="none" stroke="#1d4c85" stroke-width="2.5"/>
        <line x1="16" y1="38" x2="38" y2="16" stroke="#1d4c85" stroke-width="2.5"/>
      </svg>
      <span class="feature-divider"></span>
      <p class="feature-text">Simple and painless screening for your child</p>
    </div>

    <div class="feature-card feature-right">
      <svg class="feature-icon" viewBox="0 0 54 54">
        <circle cx="27" cy="27" r="25" fill="#fff" stroke="#1d4c85" stroke-width="4"/>
        <rect x="19" y="17" width="9" height="16" rx="3" fill="none" stroke="#1d4c85" stroke-width="2.2"/>
        <path d="M23 33 v6 a4 4 0 0 0 8 0 v-3 a4 4 0 0 1 8 0" fill="none" stroke="#1d4c85" stroke-width="2.2"/>
      </svg>
      <span class="feature-divider"></span>
      <p class="feature-text">Our Screening uses ultrasound which is transcranial doppler</p>
    </div>

    <h2 class="pill pill-facts">Key Facts</h2>

    <div class="fact fact-left" style="top:190px">
      <svg class="fact-icon" viewBox="0 0 46 46"><circle cx="23" cy="23" r="21" fill="#d8f1fb" stroke="#fff" stroke-width="3"/><circle cx="23" cy="23" r="16" fill="none" stroke="#1d4c85" stroke-width="1.6"/><circle cx="18" cy="20" r="3" fill="#1d4c85"/><circle cx="26" cy="18" r="2.5" fill="#1d4c85"/><circle cx="22" cy="28" r="3" fill="#1d4c85"/></svg>
      <p class="fact-text">Sickle cell disease (SCD) is a blood disorder in which misshapen or “sickled” red blood cells can clog blood vessels and cause complications such as stroke and blood vessel damage</p>
    </div>
    <div class="fact fact-left" style="top:294px">
      <svg class="fact-icon" viewBox="0 0 46 46"><circle cx="23" cy="23" r="21" fill="#d8f1fb" stroke="#fff" stroke-width="3"/><path d="M17 12 C31 20 15 26 29 34 M29 12 C15 20 31 26 17 34" fill="none" stroke="#1d4c85" stroke-width="2"/></svg>
      <p class="fact-text">The most severe form of the disease, called sickle cell anemia, occurs when a person inherits two abnormal copies of the hemoglobin-Beta gene</p>
    </div>
    <div class="fact fact-left" style="top:381px">
      <svg class="fact-icon" viewBox="0 0 46 46"><circle cx="23" cy="23" r="21" fill="#d8f1fb" stroke="#fff" stroke-width="3"/><ellipse cx="23" cy="22" rx="13" ry="10" fill="none" stroke="#1d4c85" stroke-width="1.8"/><line x1="23" y1="12" x2="23" y2="32" stroke="#1d4c85" stroke-width="1.5"/></svg>
      <p class="fact-text">Stroke risk increases over 100-fold in children with SCD compared to children without sickle cell disease</p>
    </div>

    <div class="fact fact-right" style="top:190px">
      <svg class="fact-icon" viewBox="0 0 46 46"><circle cx="23" cy="23" r="21" fill="#d8f1fb" stroke="#fff" stroke-width="3"/><circle cx="23" cy="17" r="7" fill="none" stroke="#1d4c85" stroke-width="1.8"/><path d="M14 34 a9 9 0 0 1 18 0" fill="none" stroke="#1d4c85" stroke-width="1.8"/></svg>
      <p class="fact-text">All babies in the U.S. are screened for sickle cell disease, which affects 1 in 2,400 children, and 1 in 400 Black children</p>
    </div>
    <div class="fact fact-right" style="top:258px">
      <svg class="fact-icon" viewBox="0 0 46 46"><circle cx="23" cy="23" r="21" fill="#d8f1fb" stroke="#fff" stroke-width="3"/><text x="23" y="28" text-anchor="middle" font-family="Mystery Quest, cursive" font-size="16" fill="#1d4c85">11%</text></svg>
      <p class="fact-text">About 11% of SCD patients have strokes before age 20 with the highest risk between age 2 and 5</p>
    </div>
    <div class="fact fact-right" style="top:326px">
      <svg class="fact-icon" viewBox="0 0 46 46"><circle cx="23" cy="23" r="21" fill="#d8f1fb" stroke="#fff" stroke-width="3"/><rect x="12" y="14" width="22" height="15" rx="7" fill="none" stroke="#1d4c85" stroke-width="1.8"/><path d="M17 29 l-2 5 l6 -5" fill="none" stroke="#1d4c85" stroke-width="1.8"/><circle cx="32" cy="30" r="4" fill="#1d4c85"/></svg>
      <p class="fact-text">The common stroke in children with sickle cell disease is “silent strokes,” or “silent” injury to the brain.</p>
    </div>
    <div class="fact fact-right" style="top:393px">
      <svg class="fact-icon" viewBox="0 0 46 46"><circle cx="23" cy="23" r="21" fill="#d8f1fb" stroke="#fff" stroke-width="3"/><path d="M16 34 v-6 a9 9 0 1 1 14 -3 v9" fill="none" stroke="#1d4c85" stroke-width="1.8"/><path d="M24 12 l-3 6 h4 l-3 6" fill="none" stroke="#1d4c85" stroke-width="1.6"/></svg>
      <p class="fact-text">There are two main types of strokes: Ischemicand hemorrhagic. Ischemic strokes are more common in children</p>
    </div>
  </section>

  <section class="closing"></section>

  <aside class="callout">
    <div class="callout-inner">
      <p class="callout-head">Screening or early signs of stroke</p>
      <p class="callout-body">can be a tool to for early diagnosis allowing for treatments that eliminate the risk</p>
    </div>
  </aside>

  <p class="tagline">
    <svg class="tagline-star" viewBox="0 0 20 20"><path d="M10 1 L12.6 7.2 L19 7.6 L14 11.8 L15.6 18.4 L10 14.8 L4.4 18.4 L6 11.8 L1 7.6 L7.4 7.2 Z"/></svg>
    <span>Protect your childs future</span>
    <svg class="tagline-star" viewBox="0 0 20 20"><path d="M10 1 L12.6 7.2 L19 7.6 L14 11.8 L15.6 18.4 L10 14.8 L4.4 18.4 L6 11.8 L1 7.6 L7.4 7.2 Z"/></svg>
  </p>

  <footer class="footer">
    <svg class="footer-band" viewBox="0 0 864 47" preserveAspectRatio="none">
      <defs>
        <linearGradient id="footerLight" x1="0" y1="0" x2="1" y2="0">
          <stop offset="0" stop-color="#7cc0e8"/>
          <stop offset="1" stop-color="#3f8fd0"/>
        </linearGradient>
      </defs>
      <rect x="0" y="8" width="864" height="39" fill="url(#footerLight)"/>
      <path d="M348 47 L385 0 L864 0 L864 47 Z" fill="#1d4c85"/>
    </svg>
    <p class="footer-web" style="top:4px">Visit: <strong>www.brightpathwellbeing.net</strong></p>
    <p class="footer-call">Call to schedule: <strong>833-412-7086</strong></p>
  </footer>

</main>
</body>
</html>
```